Business Card Design

I already have a company logo for my company. I have a logo for the manufacturer we represent. I want a professional business card design.

```html
<!DOCTYPE html>
<html lang="en">
<head>
<meta charset="utf-8">
<title>Beacon Guard Group – Business Card</title>
<link href="https://fonts.googleapis.com/css2?family=Montserrat:wght@400;500;700;800&display=swap" rel="stylesheet">
<style>
  :root {
    --backdrop: #e9e6e1;
    --card-dark: #1c1c1e;
    --card-dark-top: #333336;
    --card-white: #ffffff;
    --brand-red: #e0262e;
    --brand-silver: #d6d6d8;
    --ink: #3a3a3a;
    --ink-soft: #5a5a5a;
    --shadow: rgba(0,0,0,0.22);
  }
  * { margin: 0; padding: 0; box-sizing: border-box; }
  html, body {
    width: 1200px; height: 913px; overflow: hidden;
    background: var(--backdrop);
    font-family: "Montserrat", sans-serif;
  }
  .sheet {
    width: 1200px; height: 913px;
    display: flex; align-items: center; justify-content: center; gap: 44px;
  }
  .card {
    position: relative;
    width: 520px; height: 297px;
    border-radius: 4px;
    overflow: hidden;
    box-shadow: 0 14px 30px var(--shadow);
  }

  /* Front */
  .card--front {
    background: linear-gradient(160deg, var(--card-dark-top), var(--card-dark) 70%);
    display: flex; align-items: center; justify-content: center;
  }
  .wordmark {
    display: flex; align-items: center; gap: 14px;
    color: var(--brand-silver);
    font-weight: 800;
    text-transform: uppercase;
    letter-spacing: 1px;
    line-height: 1.05;
  }
  .wordmark__square {
    width: 34px; height: 34px; background: var(--brand-red); flex: none;
  }
  .card--front .wordmark { font-size: 32px; }

  /* Back */
  .card--back { background: var(--card-white); }
  .back__wave { position: absolute; inset: 0; }
  .card--back .wordmark {
    position: absolute; top: 34px; right: 40px;
    font-size: 22px;
    color: var(--brand-red);
  }
  .card--back .wordmark__square { width: 24px; height: 24px; }

  .person {
    position: absolute; top: 92px; left: 0;
    padding-left: 34px;
  }
  .person__bar {
    position: absolute; left: 0; top: 2px;
    width: 10px; height: 40px; background: var(--brand-red);
  }
  .person__name {
    font-size: 19px; font-weight: 700; color: var(--brand-red);
  }
  .person__title {
    font-size: 11px; font-weight: 500; color: var(--ink-soft); margin-top: 2px;
  }

  .contacts {
    position: absolute; left: 34px; top: 172px;
    list-style: none;
  }
  .contacts__item {
    display: flex; align-items: center; gap: 10px;
    font-size: 11px; color: var(--ink); margin-bottom: 6px;
  }
  .contacts__icon { width: 11px; height: 11px; flex: none; }

  .address {
    position: absolute; right: 28px; top: 236px;
    font-size: 11px; color: #ffffff; font-weight: 500;
    white-space: nowrap;
  }
</style>
</head>
<body>
<main class="sheet">

  <section class="card card--front" aria-label="Card front">
    <div class="wordmark">
      <span class="wordmark__square"></span>
      <span>Beacon Guard<br>Group</span>
    </div>
  </section>

  <section class="card card--back" aria-label="Card back">
    <svg class="back__wave" viewBox="0 0 520 297" width="520" height="297" aria-hidden="true">
      <path d="M0,282 C200,282 270,250 340,175 C390,120 430,100 520,96 L520,297 L0,297 Z" fill="var(--card-dark)"/>
      <path d="M0,279 C200,279 270,247 340,172 C390,117 430,97 520,93" fill="none" stroke="var(--brand-red)" stroke-width="3"/>
    </svg>

    <div class="wordmark">
      <span class="wordmark__square"></span>
      <span>Beacon Guard<br>Group</span>
    </div>

    <div class="person">
      <span class="person__bar"></span>
      <p class="person__name">Daniel Reyes</p>
      <p class="person__title">Managing Director</p>
    </div>

    <ul class="contacts">
      <li class="contacts__item">
        <svg class="contacts__icon" viewBox="0 0 12 12"><path d="M2.5 1h2l1 3-1.3 1a6 6 0 0 0 2.8 2.8l1-1.3 3 1v2a1 1 0 0 1-1 1A9.5 9.5 0 0 1 1.5 2a1 1 0 0 1 1-1z" fill="var(--brand-red)"/></svg>
        555.210.0198
      </li>
      <li class="contacts__item">
        <svg class="contacts__icon" viewBox="0 0 12 12"><rect x="0.5" y="2" width="11" height="8" rx="1" fill="var(--brand-red)"/><path d="M1 3l5 3.5L11 3" fill="none" stroke="#fff" stroke-width="1"/></svg>
        hello@beaconguardgroup.com
      </li>
      <li class="contacts__item">
        <svg class="contacts__icon" viewBox="0 0 12 12"><circle cx="6" cy="6" r="5.2" fill="var(--brand-red)"/><path d="M1 6h10M6 0.8c-2.4 3-2.4 7.4 0 10.4M6 0.8c2.4 3 2.4 7.4 0 10.4" fill="none" stroke="#fff" stroke-width="0.8"/></svg>
        www.beaconguardgroup.com
      </li>
    </ul>

    <p class="address">240 Maple Ave Springfield, CO 80000</p>
  </section>

</main>
</body>
</html>
```